Form With Marla - Health and Wellness Business Card and Logo

I need a business card design with a logo for my business you can check out at www.formwithmarla.net. I want something more original, simplistic, and memorable than the basic logo I have on my site currently. I am a health and wellness coach and I offer mindset coaching and nutrition plans. I like the colour teal and dark grey/black for my theme colours. I emphasize growth, longterm change, and the whole package of "healthy mind, healthy body, healthy life". I had played around the idea of intertwining 3 M's or incorporating growth (leaves etc.) into my design. I want my expertise and experience to show through. In one glance I want people to understand with confidence I can help them accomplish anything they set their minds to. I look forward to seeing what everyone comes up with!

Industry/Entity Type

Health And Wellness

Contact Information for Business Card

Form With Marla
Marla Prentiss
BSc, Health & Wellness Coach
"Shape your finest"
www.formwithmarla.net
formwithmarla@quillpost.net
472-618-9043

Colors
33b8a4
ffffff
333333
000000

Requirements
Must have
• A memorable and unique logo for my business!
Nice to have
• Could have the phrase "Are you unhappy with your body and state of health?" or "It takes the right skills to develop habits in order to create long term change. I can help you get there."

```html
<!DOCTYPE html>
<html lang="en">
<head>
<meta charset="utf-8">
<title>Form With Marla – Business Card</title>
<link rel="stylesheet" href="https://fonts.googleapis.com/css2?family=Questrial&family=Open+Sans:wght@400;600;700&display=swap">
<style>
  :root {
    --page: #e9ecec;
    --card-dark: #262626;
    --card-dark-edge: #1c1c1c;
    --ink: #333333;
    --ink-soft: #4a4a4a;
    --logo-grey: #8c8c8c;
    --teal-light: #bfe7ea;
    --teal-mid: #a6dde2;
    --teal-deep: #8fd1d8;
    --white: #ffffff;
  }
  * { box-sizing: border-box; margin: 0; padding: 0; }
  html, body {
    width: 1200px; height: 1000px; overflow: hidden;
    background: var(--page);
  }
  .canvas {
    width: 1200px; height: 1000px;
    display: flex; flex-direction: column;
    align-items: center; justify-content: center; gap: 60px;
  }
  .card {
    width: 700px; height: 400px; position: relative;
    border-radius: 4px;
    box-shadow: 0 10px 30px rgba(0,0,0,0.18);
    overflow: hidden;
  }

  /* Front */
  .card--front { background: radial-gradient(ellipse at 50% 40%, #2e2e2e, var(--card-dark-edge)); }
  .front-mark {
    position: absolute; left: 0; right: 0; top: 140px;
    display: flex; flex-direction: column; align-items: center;
  }
  .front-mark__rule { width: 250px; height: 1px; background: var(--logo-grey); margin-bottom: 10px; }
  .front-mark__name {
    font-family: "Questrial", sans-serif; font-size: 34px;
    color: var(--logo-grey); letter-spacing: 0.5px;
  }
  .tagline {
    position: absolute; left: 0; right: 0; bottom: 42px; text-align: center;
    font-family: "Open Sans", sans-serif; font-size: 16px; color: var(--white);
    letter-spacing: 5px;
  }

  /* Back */
  .card--back {
    background:
      radial-gradient(ellipse at 70% 30%, rgba(255,255,255,0.35), transparent 60%),
      radial-gradient(ellipse at 20% 90%, var(--teal-deep), transparent 55%),
      linear-gradient(135deg, var(--teal-mid), var(--teal-light) 50%, var(--teal-mid));
  }
  .brand-title {
    position: absolute; left: 56px; top: 38px;
    font-family: "Questrial", sans-serif; font-weight: 400; font-size: 42px; color: var(--ink);
  }
  .tab {
    position: absolute; left: 0; top: 110px; width: 10px; height: 38px;
    background: var(--ink); border-radius: 0 4px 4px 0;
  }
  .person { position: absolute; left: 56px; top: 112px; font-family: "Open Sans", sans-serif; }
  .person__name { font-size: 28px; font-weight: 700; color: var(--ink); letter-spacing: 0.5px; }
  .person__role { font-size: 15px; font-weight: 600; color: var(--ink-soft); margin-top: -2px; }
  .contacts {
    position: absolute; left: 40px; top: 222px; list-style: none;
    font-family: "Open Sans", sans-serif; font-size: 17px; color: var(--ink);
  }
  .contacts li { display: flex; align-items: center; gap: 12px; height: 26px; }
  .contacts svg { width: 14px; height: 14px; fill: var(--ink); flex: none; }
  .contacts .web b { font-weight: 700; }
  .back-mark {
    position: absolute; right: 44px; bottom: 40px;
    font-family: "Questrial", sans-serif; font-size: 26px; color: var(--white);
  }
</style>
</head>
<body>
<main class="canvas">
  <section class="card card--front" aria-label="Card front">
    <div class="front-mark">
      <div class="front-mark__rule"></div>
      <div class="front-mark__name">Form With Marla</div>
    </div>
    <p class="tagline">"Shape your finest"</p>
  </section>

  <section class="card card--back" aria-label="Card back">
    <h1 class="brand-title">Form With Marla</h1>
    <div class="tab"></div>
    <div class="person">
      <div class="person__name">MARLA PRENTISS</div>
      <div class="person__role">BSc, Health &amp; Wellness Coach</div>
    </div>
    <ul class="contacts">
      <li>
        <svg viewBox="0 0 24 24"><path d="M6.6 10.8a15 15 0 0 0 6.6 6.6l2.2-2.2a1 1 0 0 1 1-.25 11.4 11.4 0 0 0 3.6.57 1 1 0 0 1 1 1V20a1 1 0 0 1-1 1A17 17 0 0 1 3 4a1 1 0 0 1 1-1h3.5a1 1 0 0 1 1 1c0 1.25.2 2.45.57 3.57a1 1 0 0 1-.25 1z"/></svg>
        472-618-9043
      </li>
      <li>
        <svg viewBox="0 0 24 24"><path d="M2 5h20v14H2z M2 5l10 8 10-8" fill="none" stroke="#333" stroke-width="2"/></svg>
        formwithmarla@quillpost.net
      </li>
      <li class="web">
        <svg viewBox="0 0 24 24"><circle cx="12" cy="12" r="10"/></svg>
        <span>www.<b>formwithmarla</b>.net</span>
      </li>
      <li>
        <svg viewBox="0 0 24 24"><circle cx="12" cy="12" r="9" fill="none" stroke="#333" stroke-width="2.5"/></svg>
        @marlaprentiss
      </li>
    </ul>
    <div class="back-mark">Form With Marla</div>
  </section>
</main>
</body>
</html>
```